BGC Business Card

Looking for a business card design to incorporate our branding. We want to only use the colors listing in the Branding Package (attached).
Updates

Target Market(s)

People who need their phone or device fixed.

Industry/Entity Type

Electronics

Contact Information for Business Card

Please use:

Brightwick Gadget Clinic LLC
4810 E Harlow Ridge Rd
Suite 417
San Antonio, TX 78163

Marcus Delgrove, Store Manager

(210) 555-0147

Requirements
Must have
• Must include the colors that are contained within the Branding Package PDF file.

```html
<!DOCTYPE html>
<html lang="en">
<head>
<meta charset="utf-8">
<title>Brightwick Gadget Clinic Business Card</title>
<link rel="stylesheet" href="https://fonts.googleapis.com/css2?family=Arimo:wght@400;700&display=swap">
<style>
  :root {
    --stage: #2b2d31;
    --card: #ffffff;
    --brand-orange: #f05a28;
    --band-grey: #6e6e6e;
    --ink: #333333;
    --ink-soft: #444444;
  }
  html, body {
    margin: 0;
    padding: 0;
    width: 1200px;
    height: 960px;
    overflow: hidden;
    background: var(--stage);
    font-family: "Arimo", Arial, sans-serif;
  }
  .canvas {
    position: relative;
    width: 1200px;
    height: 960px;
  }
  .card {
    position: absolute;
    width: 560px;
    height: 320px;
    background: var(--card);
    box-shadow: 0 10px 30px rgba(0,0,0,0.45);
    overflow: hidden;
  }
  .card-front { left: 90px; top: 90px; }
  .card-back { left: 550px; top: 530px; }

  .brand {
    display: flex;
    align-items: center;
    justify-content: center;
    gap: 10px;
  }
  .brand-mark {
    width: 26px;
    height: 26px;
    background: var(--brand-orange);
    border-radius: 4px;
  }
  .brand-name {
    color: var(--brand-orange);
    font-weight: 400;
    font-size: 26px;
    letter-spacing: 0.3px;
    white-space: nowrap;
  }
  .card-front .brand {
    position: absolute;
    left: 0; right: 0; top: 142px;
  }
  .card-back .brand {
    position: absolute;
    left: 0; right: 0; top: 38px;
  }
  .card-back .brand-name { font-size: 28px; }
  .card-back .brand-mark { width: 30px; height: 30px; }

  .person {
    position: absolute;
    top: 94px;
    left: 0; right: 0;
    text-align: center;
  }
  .person-name {
    font-size: 22px;
    color: var(--ink);
    line-height: 1.1;
  }
  .person-title {
    font-size: 13px;
    color: var(--brand-orange);
  }
  .details {
    position: absolute;
    top: 160px;
    left: 0; right: 0;
    display: flex;
    justify-content: center;
  }
  .address {
    width: 232px;
    text-align: right;
    font-size: 15px;
    line-height: 1.35;
    color: var(--ink-soft);
    padding-right: 16px;
    padding-top: 18px;
    white-space: nowrap;
  }
  .divider {
    width: 2px;
    height: 80px;
    background: var(--ink-soft);
  }
  .contacts {
    width: 270px;
    padding-left: 14px;
    font-size: 15px;
    color: var(--ink-soft);
  }
  .contact-row {
    display: flex;
    align-items: center;
    gap: 8px;
    line-height: 24px;
    white-space: nowrap;
  }
  .contact-row svg { flex: none; }
  .band {
    position: absolute;
    left: 0; right: 0;
    top: 258px;
    height: 36px;
    background: var(--band-grey);
    color: #ffffff;
    font-size: 15px;
    text-align: center;
    line-height: 36px;
    letter-spacing: 0.4px;
  }
</style>
</head>
<body>
<main class="canvas">
  <section class="card card-front" aria-label="Card front">
    <div class="brand">
      <span class="brand-mark"></span>
      <span class="brand-name">Brightwick Gadget Clinic</span>
    </div>
  </section>

  <section class="card card-back" aria-label="Card back">
    <div class="brand">
      <span class="brand-mark"></span>
      <span class="brand-name">Brightwick Gadget Clinic</span>
    </div>
    <div class="person">
      <div class="person-name">Marcus Delgrove</div>
      <div class="person-title">Store Manager</div>
    </div>
    <div class="details">
      <div class="address">
        4810 E Harlow Ridge Rd<br>
        Suite 417<br>
        San Antonio, TX 78163
      </div>
      <div class="divider"></div>
      <div class="contacts">
        <div class="contact-row">
          <svg width="16" height="16" viewBox="0 0 16 16" aria-hidden="true">
            <rect width="16" height="16" rx="2" fill="var(--brand-orange)"/>
            <path d="M5 3.5c.6 0 1 .9 1.3 1.8.2.6-.6 1-.6 1.4.3 1.3 1.3 2.3 2.6 2.6.4 0 .8-.8 1.4-.6.9.3 1.8.7 1.8 1.3 0 .8-1 1.7-2 1.7C6.6 11.7 4.3 9.4 4.3 5.5c0-1 .9-2 .7-2z" fill="#fff"/>
          </svg>
          <span>(210) 555-0147</span>
        </div>
        <div class="contact-row">
          <svg width="16" height="16" viewBox="0 0 16 16" aria-hidden="true">
            <rect width="16" height="16" rx="2" fill="var(--brand-orange)"/>
            <rect x="3" y="4.5" width="10" height="7" fill="#fff"/>
            <path d="M3 4.5l5 4 5-4" fill="none" stroke="var(--brand-orange)" stroke-width="1"/>
          </svg>
          <span>marcus@BrightwickClinic.com</span>
        </div>
      </div>
    </div>
    <div class="band">www.BrightwickClinic.com</div>
  </section>
</main>
</body>
</html>
```